Lush Satchel

I am developing a web site which sells preowned high end designer handbags and accessories. Some of the brands include: Varenne, Marcel Ostrand & Belmo, to name a few. I am after a luxurious and high end feel.

Some brands I like that express this feel include: Quintel, Belmo, fabcloset.com, pursepassonpaw.com

I am after a logo, business card, letterhead, with compliments, address label and envelope designs.
The business name is Lush satchel, and the website will be www.lushsatchel.com.au. I have thoughts of using LSC as a logo or LUSH satchel.com.au

I don't want a large logo, it needs to blend in with the name in some way - or may not need an image at all, if the style of the font speaks to the brand.

Thank-you
Updates

Project Deadline Extended
Reason: I would like to give designers plenty of time to be able to submit a design.

Target Market(s)

Women, aged 25-60 who are into fashion

Industry/Entity Type

Business

Requirements
Must have
• High End
Luxurious

```html
<!DOCTYPE html>
<html lang="en">
<head>
<meta charset="utf-8">
<title>Lush Satchel — Stationery Set</title>
<link rel="stylesheet" href="https://fonts.googleapis.com/css2?family=Ubuntu:wght@400;500&display=swap">
<style>
  :root {
    --crimson: #bd1f3f;
    --ink: #1a1a1a;
    --paper: #ffffff;
    --line: #222222;
    --font: "Ubuntu", sans-serif;
  }
  html, body {
    margin: 0;
    padding: 0;
    overflow: hidden;
    background: var(--paper);
  }
  .sheet {
    position: relative;
    width: 1131px;
    height: 1200px;
    overflow: hidden;
    font-family: var(--font);
    background: var(--paper);
  }
  .shapes {
    position: absolute;
    inset: 0;
  }
  .text {
    position: absolute;
    margin: 0;
    white-space: nowrap;
    line-height: 1;
  }
  .brand-name {
    color: var(--crimson);
    font-weight: 500;
  }
  .brand-url {
    color: var(--ink);
    font-weight: 400;
  }

  /* Primary logo */
  .logo-main .brand-name { left: 70px; top: 150px; font-size: 60px; }
  .logo-main-url { left: 87px; top: 366px; font-size: 29px; letter-spacing: 0.5px; }

  /* Long envelope */
  .envelope-url { left: 472px; top: 213px; font-size: 19px; color: var(--ink); }

  /* Window envelope */
  .window-name { left: 486px; top: 366px; font-size: 15px; }
  .window-url { left: 488px; top: 414px; font-size: 7px; }

  /* Address label */
  .label-name { left: 60px; top: 652px; font-size: 44px; color: var(--paper); font-weight: 500; }
  .label-address {
    right: 526px;
    top: 675px;
    font-size: 36px;
    color: var(--paper);
    text-align: right;
    line-height: 44px;
  }

  /* Business card */
  .card-name { left: 76px; top: 946px; font-size: 25px; }
  .card-url { left: 78px; top: 1026px; font-size: 11px; font-weight: 500; }
  .card-contact { left: 330px; top: 1015px; color: var(--paper); font-size: 20px; line-height: 33px; }
  .card-contact .email { font-size: 22px; padding-left: 6px; letter-spacing: 0.5px; }
  .card-contact .phone { font-size: 24px; padding-left: 40px; }

  /* Letterhead */
  .letter-name { left: 702px; top: 670px; font-size: 26px; }
  .letter-url { left: 708px; top: 745px; font-size: 12px; font-weight: 500; }
  .letter-contact { left: 680px; top: 1108px; color: var(--crimson); font-size: 20px; line-height: 24px; }
  .letter-contact .email { font-size: 22px; padding-left: 2px; letter-spacing: 0.5px; }
  .letter-contact .phone { font-size: 24px; padding-left: 4px; }
</style>
</head>
<body>
<main class="sheet">
  <svg class="shapes" width="1131" height="1200" viewBox="0 0 1131 1200" aria-hidden="true">
    <!-- Long envelope -->
    <rect class="envelope-frame" x="456" y="31" width="626" height="223" fill="none" stroke="var(--line)" stroke-width="2"/>
    <polygon class="envelope-flap" points="456,31 1078,33 779,155" fill="var(--crimson)"/>

    <!-- Window envelope -->
    <rect class="window-envelope-frame" x="453" y="317" width="625" height="223" fill="none" stroke="var(--line)" stroke-width="2"/>
    <rect class="address-window" x="827" y="448" width="227" height="67" rx="33" fill="none" stroke="var(--line)" stroke-width="2"/>

    <!-- Address label -->
    <rect class="address-label" x="21" y="573" width="608" height="211" rx="62" fill="var(--crimson)"/>

    <!-- Business card -->
    <rect class="card-frame" x="43" y="854" width="527" height="299" rx="68" fill="none" stroke="var(--line)" stroke-width="2"/>
    <path class="card-panel" d="M275 853 L530 853 Q570 858 570 900 L570 1115 Q568 1153 535 1154 L375 1154 C300 1110 250 1000 275 853 Z" fill="var(--crimson)"/>

    <!-- Letterhead -->
    <rect class="letterhead-frame" x="672" y="585" width="458" height="613" fill="none" stroke="var(--line)" stroke-width="2"/>
  </svg>

  <!-- Primary logo -->
  <div class="logo-main">
    <p class="text brand-name">Lush Satchel</p>
  </div>
  <p class="text brand-url logo-main-url">lushsatchel.com.au</p>

  <!-- Long envelope -->
  <p class="text envelope-url">lushsatchel.com.au</p>

  <!-- Window envelope -->
  <p class="text brand-name window-name">Lush Satchel</p>
  <p class="text brand-url window-url">lushsatchel.com.au</p>

  <!-- Address label -->
  <p class="text label-name">Lush Satchel</p>
  <p class="text label-address">48 Harbour Lane<br>WA, 6012</p>

  <!-- Business card -->
  <p class="text brand-name card-name">Lush Satchel</p>
  <p class="text brand-url card-url">lushsatchel.com.au</p>
  <p class="text card-contact">Ardena Studio<br><span class="email">xxxx@xxxxx. com</span><br><span class="phone">555•5555</span></p>

  <!-- Letterhead -->
  <p class="text brand-name letter-name">Lush Satchel</p>
  <p class="text brand-url letter-url">lushsatchel.com.au</p>
  <p class="text letter-contact">Ardena Studio<br><span class="email">xxxx@xxxxx. com</span><br><span class="phone">555•5555</span></p>
</main>
</body>
</html>
```